"Velmora Crest" sexual performance enhancement pill bottle label needed.

This should be interesting...

I am starting a line of sexual performance enhancement products. This will be the first of several products basically. Keep in mind, I am the type of business person to stay with one company for years if they provide me with quality work.

This particular product is a male sexual performance pill. The name of the product is "Velmora Crest." The packaging of the pills are a black bottle with a white top. Label on the product example would be perfect but at a minimum I have attached a "template" for your guidance.

Some of the technical aspects of this are as follows:

-File Format: Illustrator CS6 is preferred. (Winner must provide artwork in layer and can not flatten artwork.)
-Resolution: 300 dpi minimum
-Bleed: 1/16th (0.0625") inch from edge of label
-Color Mode: CMYK only or must be converted to CMYK for final production

Lastly, this is your project as a designer, artist, creator, this is essentially a piece of you that will be sold and known by thousands of people. I have no color scheme that I prefer, just use the template and follow the layout. If you have any further questions, please feel free to contact me at any time.
Updates

Quick note on the product and what it does: -Powerful, long lasting, harder erections -Works in a minutes and last for hours -Enhances sexual desire and drive Thank you for your ideas...

Project Deadline Extended
Reason: We decided to extent the project for a few more days to let the last few concepts come in. So far things are looking really good and we definitely have seen some amazing designs. Thank you for your hard work and amazing creativity. Looking forward to seeing what we have come in the next couple of day. Very respectfully, Brev

ONLY THREE DAYS LEFT!!!! Please submit your ideas as soon as possible. And as always, thank you for your help!!! V/r, Brev

Industry/Entity Type

Graphic Design

```html
<!DOCTYPE html>
<html lang="en">
<head>
<meta charset="utf-8">
<title>Velmora Crest – Bottle Label</title>
<link rel="stylesheet" href="https://fonts.googleapis.com/css2?family=Anton&family=Archivo:wght@500;700&family=Archivo+Black&display=swap">
<style>
  :root {
    --page: #ffffff;
    --label-black: #1c1c1c;
    --label-black-deep: #0c0c0c;
    --brand-red: #c4122f;
    --brand-red-dark: #7d0a1c;
    --paper: #ffffff;
    --paper-shade: #bdbdbd;
    --ink: #111111;
    --claim-white: #f2f2f2;
    --claim-grey: #6f6f6f;
    --accent-red: #e0173a;
    --lips-red: #d61f2c;
    --lips-deep: #8e0c16;
    --seal-gold: #d9a21b;
  }
  html, body {
    margin: 0;
    padding: 0;
    width: 1200px;
    height: 970px;
    overflow: hidden;
    background: var(--page);
  }
  .canvas {
    position: relative;
    width: 1200px;
    height: 970px;
  }
  .label {
    position: absolute;
    left: 80px;
    top: 185px;
    width: 1040px;
    height: 600px;
    background: linear-gradient(180deg, var(--label-black) 0%, var(--label-black-deep) 100%);
    overflow: hidden;
  }
  .label__top {
    position: absolute;
    left: 0;
    top: 0;
    width: 100%;
    height: 290px;
    background: linear-gradient(90deg, var(--paper) 0%, var(--paper) 70%, var(--paper-shade) 100%);
  }
  .name-block {
    position: absolute;
    top: 0;
    height: 290px;
    display: flex;
    align-items: center;
    justify-content: center;
  }
  .name-block--red {
    left: 0;
    width: 394px;
    background: linear-gradient(90deg, var(--brand-red-dark) 0%, var(--brand-red) 60%, var(--brand-red) 100%);
    border-top-right-radius: 14px;
    justify-content: flex-end;
    padding-right: 14px;
    box-sizing: border-box;
  }
  .name-block--white {
    left: 394px;
    width: 130px;
    background: var(--paper);
  }
  .name-word {
    font-family: "Anton", "Impact", sans-serif;
    font-weight: 400;
    font-size: 84px;
    line-height: 1;
    letter-spacing: 1px;
    color: var(--ink);
    writing-mode: vertical-rl;
    transform: rotate(180deg);
    margin: 0;
  }
  .lips-art {
    position: absolute;
    left: 536px;
    top: 34px;
    width: 270px;
    height: 160px;
    border-radius: 50% 50% 46% 46% / 55% 55% 45% 45%;
    background: radial-gradient(ellipse at 50% 50%, var(--lips-red) 0%, var(--lips-red) 55%, var(--lips-deep) 100%);
  }
  .quality-seal {
    position: absolute;
    left: 730px;
    top: 206px;
    width: 80px;
    height: 80px;
    border-radius: 50%;
    background: var(--seal-gold);
  }
  .claims {
    position: absolute;
    left: 0;
    top: 310px;
    width: 100%;
  }
  .claim-row {
    display: flex;
    height: 45px;
    align-items: center;
  }
  .claim-row__lead {
    width: 394px;
    text-align: right;
    font-family: "Archivo", "Arial", sans-serif;
    font-weight: 500;
    font-size: 37px;
    color: var(--claim-white);
    letter-spacing: -0.5px;
  }
  .claim-row__support {
    padding-left: 12px;
    font-family: "Archivo Black", "Arial Black", sans-serif;
    font-size: 36px;
    letter-spacing: 3px;
    color: var(--claim-grey);
  }
  .timing-line {
    position: absolute;
    left: 0;
    width: 920px;
    top: 448px;
    margin: 0;
    text-align: center;
    font-family: "Archivo", "Arial", sans-serif;
    font-weight: 700;
    font-size: 26px;
    color: var(--accent-red);
  }
  .count {
    position: absolute;
    left: 0;
    width: 920px;
    top: 548px;
    margin: 0;
    text-align: center;
    font-family: "Archivo", "Arial", sans-serif;
    font-weight: 700;
    font-size: 32px;
    color: var(--claim-grey);
  }
  .count__unit {
    font-size: 17px;
    margin-left: 4px;
  }
</style>
</head>
<body>
  <div class="canvas">
    <section class="label">
      <div class="label__top">
        <div class="name-block name-block--red">
          <h1 class="name-word">VELMORA</h1>
        </div>
        <div class="name-block name-block--white">
          <span class="name-word">CREST</span>
        </div>
        <div class="lips-art" role="img" aria-label="Red lipstick kiss print"></div>
        <div class="quality-seal" role="img" aria-label="Quality seal"></div>
      </div>

      <div class="claims">
        <div class="claim-row">
          <span class="claim-row__lead">POWERFUL</span>
          <span class="claim-row__support">ENHANCES</span>
        </div>
        <div class="claim-row">
          <span class="claim-row__lead">LONG LASTING</span>
          <span class="claim-row__support">SEXUAL DESIRE</span>
        </div>
        <div class="claim-row">
          <span class="claim-row__lead">HARDER ERECTIONS</span>
          <span class="claim-row__support">AND DRIVE</span>
        </div>
      </div>

      <p class="timing-line">WORKS IN A MINUTES AND LAST FOR HOURS</p>
      <p class="count">60<span class="count__unit">TABLETS</span></p>
    </section>
  </div>
</body>
</html>
```